Vetern Mailer for Mortgage Refinance

Hello, I need some options in my KB mailers we send out here in the USA! A sample of our mailer has been included. I need all the verbiage the same. The data merge points need to stay on too. Please make this pop. We have a high end PELDO printer and a Z auto folding machine. Letter goes into a number 10 envelope with windows. So lets see what you can do. One with colors below is our company colors and then one black, white, gray.
Blue - 3399FF------ R 51 G 153 B 255
Orange - FF9933----- R 255 G 153 B 51
Black – 333333------ R 51 G 51 B 51
White – FFFFFF------ R 255 G 255 B 255

Target Market(s)

United States Military Service Members

Industry/Entity Type

Mortgage Lender

Requirements
Must have
• Margins for folding with Z and Number 10 Envelope with two windows

```html
<!DOCTYPE html>
<html lang="en">
<head>
<meta charset="utf-8">
<title>Summit Crest Home Loans – KB Refinance Letter</title>
<link href="https://fonts.googleapis.com/css2?family=Poppins:wght@300;400;500;600;700;800&family=Arimo:wght@400&display=swap" rel="stylesheet">
<style>
  :root{
    --blue:#3399ff;
    --orange:#ff9933;
    --ink:#333333;
    --white:#ffffff;
    --stage:#5f5f5f;
    --band:#e3e3e3;
  }
  *{box-sizing:border-box;margin:0;padding:0}
  html,body{width:1200px;height:2604px;overflow:hidden}
  body{background:var(--stage);position:relative;font-family:'Poppins',sans-serif;color:var(--ink)}
  .letter{position:absolute;left:50px;top:598px;width:820px;height:1050px;background:var(--white);
    transform:scale(1.3415);transform-origin:0 0;box-shadow:0 4px 14px rgba(0,0,0,.25)}
  .letter > *{position:absolute}
  .reference{left:75px;top:28px;font-family:'Arimo',sans-serif;font-size:15px;line-height:21px}
  .notice{left:51px;top:116px;font-family:'Arimo',sans-serif;font-size:11px;line-height:15px}
  .recipient{left:75px;top:170px;font-family:'Arimo',sans-serif;font-size:15px;line-height:21px}
  .brand{left:478px;top:100px;width:282px;text-align:center;white-space:nowrap;font-weight:300;font-size:30px;letter-spacing:2px;color:var(--blue);line-height:44px}
  .contact-box{left:483px;top:168px;width:268px;height:80px;border:2px solid var(--orange);border-radius:9px;
    display:flex;flex-direction:column;justify-content:center;align-items:center;font-weight:600;font-size:14.5px;line-height:27px}
  .greeting{left:75px;top:320px;color:var(--blue);font-weight:600;font-size:16.5px}
  .body-copy{left:75px;top:356px;width:390px;font-size:14.3px;line-height:22.8px}
  .body-copy .amount{color:var(--blue);font-weight:600}
  sup{font-size:7px;vertical-align:super;line-height:0}
  .escrow{left:75px;top:604px;width:400px;font-weight:700;font-size:17.5px;line-height:23px}
  .offer{left:490px;top:330px;width:266px;height:316px;border:2px solid var(--blue);border-radius:12px;text-align:center}
  .offer-head{background:var(--blue);color:var(--white);border-radius:10px 10px 12px 12px;height:135px;padding-top:14px;font-weight:600;font-size:16px;line-height:24px}
  .offer-amount{font-weight:800;font-size:56px;line-height:66px}
  .offer-text{margin-top:12px;font-size:17px;line-height:24px;font-weight:400}
  .toll{display:inline-block;margin-top:12px;background:var(--orange);color:var(--white);font-weight:600;font-size:14px;padding:1px 26px;
    clip-path:polygon(10px 0,calc(100% - 10px) 0,100% 50%,calc(100% - 10px) 100%,10px 100%,0 50%)}
  .offer-phone{color:var(--blue);font-weight:700;font-size:23px;line-height:30px;margin-top:2px}
  .offer-hours{font-size:13px}
  .benefits{top:670px;height:152px;border:1.5px solid var(--orange);border-radius:10px;overflow:hidden}
  .benefits.cashout{left:83px;width:320px}
  .benefits.irrrl{left:433px;width:306px}
  .benefits h3{background:var(--orange);color:var(--white);font-weight:600;font-size:14.5px;height:26px;line-height:26px;padding-left:12px;letter-spacing:.3px}
  .benefits ul{list-style:none;padding:10px 0 0 14px;font-weight:600;font-size:12.3px;line-height:20px}
  .benefits li::before{content:"•";margin-right:9px}
  .closing{left:70px;top:838px;width:690px;font-size:14.5px;line-height:23px}
  .cashout-banner{left:132px;top:950px;width:538px;height:32px;background:var(--band);text-align:center;font-weight:600;font-size:16px;line-height:32px;
    clip-path:polygon(14px 0,calc(100% - 14px) 0,100% 50%,calc(100% - 14px) 100%,14px 100%,0 50%)}
  .rule{top:990px;height:4px}
  .rule.blue{left:0;width:526px;background:var(--blue)}
  .rule.orange{left:526px;width:294px;background:var(--orange)}
  .footer-company{left:70px;top:1004px;font-weight:700;font-size:10px}
  .footer-address{left:70px;top:1021px;font-size:10.5px;color:#555}
  .footer-note{left:552px;top:1022px;font-weight:700;font-size:10px;font-style:italic}
</style>
</head>
<body>
<main class="letter">
  <div class="reference">RE: &lt;&lt;lender&gt;&gt;<br>Loan ID Number: &lt;&lt;loan_id&gt;&gt;</div>
  <div class="notice">Summit Crest Home Loans LLC Is not affiliated with your<br>current lender nor is it an agency of the Federal Government.</div>
  <div class="recipient">&lt;&lt;first_name&gt;&gt; &lt;&lt;last_name&gt;&gt;<br>&lt;&lt;address&gt;&gt;<br>&lt;&lt;city_state_zip&gt;&gt;</div>

  <div class="brand">SUMMIT CREST</div>
  <div class="contact-box">
    <span>Phone: &lt;&lt;phone number&gt;&gt;</span>
    <span>Loan ID Number: &lt;&lt;loan_id&gt;&gt;</span>
  </div>

  <div class="greeting">Dear &lt;&lt;first_name&gt;&gt;,</div>
  <p class="body-copy">We are contacting you regarding your &lt;&lt;balance&gt;&gt; KB loan. Our review has indicated that because of homes appreciating in &lt;&lt;city&gt;&gt;, you may now qualify for additional benefits. These benefits may include lowering your monthly mortgage payment, deferring up to two payments, refund of escrow, and <span class="amount">$35,000</span> or more cash-out.<sup>3</sup> Call our KB Program Specialist at &lt;&lt;phone_number&gt;&gt; at your earliest convenience to receive a detailed explanation of how you may be able to access these benefits.<sup>4</sup></p>
  <p class="escrow">You may also receive a check back &nbsp;from your escrow account.<sup>2</sup></p>

  <section class="offer">
    <div class="offer-head">
      &lt;&lt;close_month&gt;&gt; &amp;<br>&lt;&lt;skip_month&gt;&gt;
      <div class="offer-amount">$000</div>
    </div>
    <p class="offer-text">You may be able to defer<br>your next two payments.<sup>1</sup></p>
    <div class="toll">CALL TOLL-FREE</div>
    <div class="offer-phone">&lt;&lt;phone_number&gt;&gt;</div>
    <div class="offer-hours">Weekdays 6 a.m. to 5 p.m. PST</div>
  </section>

  <section class="benefits cashout">
    <h3>ADDITIONAL BENEFITS INCLUDE:</h3>
    <ul>
      <li>100% LTV Cash-Out Available</li>
      <li>Pay off High Interest Debt</li>
      <li>Complete a long overdue home renovation</li>
      <li>No out-of-pocket appraisal deposit</li>
      <li>No Private Mortgage Insurance</li>
    </ul>
  </section>
  <section class="benefits irrrl">
    <h3>KB IRRRL BENEFITS:</h3>
    <ul>
      <li>Reduce Your Current Interest Rate</li>
      <li>Mortgage-Only Credit Report</li>
      <li>No Appraisal Required</li>
      <li>Fast Closings in 8-14 days</li>
      <li>No Income or Asset Verification Required</li>
    </ul>
  </section>

  <p class="closing">We recommend you call our office at &lt;&lt;phone_number&gt;&gt; within the next 3-5 business days as market rates fluctuate. By taking action now your next mortgage payment may not be due until &lt;&lt;next_pay_month&gt;&gt;.2 To avoid further delay, please call today.</p>

  <div class="cashout-banner">Cash Out Options (Tax Free): &nbsp;$35,000 or more</div>
  <div class="rule blue"></div>
  <div class="rule orange"></div>

  <div class="footer-company">Summit Crest Home Loans LLC</div>
  <div class="footer-address">NMLS 4471203 2200 &nbsp;| &nbsp;W Harbor Ave &nbsp;| &nbsp;Ste 120 &nbsp;| &nbsp;Tempe &nbsp;&nbsp;| AZ 85281</div>
  <div class="footer-note">*Please see reverse for disclaimer &gt;&gt;&gt;</div>
</main>
</body>
</html>
```